Moravel Aesthetic Doctor

I require an elegant, luxurious looking business card for my aesthetic business. I am a doctor and that will set me aside from competitors. I am planning to provide home and spa based treatments to clients with high expectations. I have attached my logo.

```html
<!DOCTYPE html>
<html lang="en">
<head>
<meta charset="utf-8">
<title>Moravel Aesthetic Doctor – Business Card</title>
<link href="https://fonts.googleapis.com/css2?family=Montserrat:wght@400;500&display=swap" rel="stylesheet">
<style>
  :root {
    --backdrop: #dcdde2;
    --card: #fbfbfb;
    --ink: #3a3c40;
    --ink-soft: #8a8e94;
    --brand-blue: #2f86c8;
    --wave-light: #a9dbf2;
    --wave-mid: #5fb6e4;
    --wave-deep: #2a78c2;
    --card-shadow: rgba(60, 62, 72, 0.28);
  }
  * { margin: 0; padding: 0; box-sizing: border-box; }
  html, body {
    width: 1200px; height: 800px; overflow: hidden;
    background: var(--backdrop);
    font-family: "Montserrat", Arial, sans-serif;
    color: var(--ink);
  }
  .canvas { position: relative; width: 1200px; height: 800px; }

  .card {
    position: absolute;
    left: 389px; width: 461px; height: 263px;
    background: var(--card);
    box-shadow: -4px 10px 14px var(--card-shadow);
  }
  .card--front { top: 93px; }
  .card--back  { top: 422px; }

  /* Front */
  .brand {
    position: absolute; left: 96px; top: 55px;
    display: flex; align-items: center; gap: 12px;
  }
  .brand__dot {
    width: 62px; height: 62px; border-radius: 50%;
    background: var(--wave-mid);
  }
  .brand__name {
    color: var(--ink-soft); font-weight: 400; line-height: 1;
  }
  .brand__title { display: block; font-size: 34px; letter-spacing: 3px; }
  .brand__tagline { display: block; font-size: 14.5px; letter-spacing: 2.2px; margin-top: 6px; }

  .services {
    position: absolute; left: 0; right: 0; top: 186px;
    text-align: center; font-size: 11px; line-height: 13.5px;
  }
  .services__offer {
    display: block; margin-top: 3px;
    font-size: 14.5px; color: var(--brand-blue); letter-spacing: 0.2px;
  }

  /* Back */
  .doctor { position: absolute; left: 25px; top: 23px; }
  .doctor__name { font-size: 13px; font-weight: 500; color: var(--brand-blue); }
  .doctor__post { font-size: 7px; color: var(--ink); margin-left: 2px; letter-spacing: 0.3px; }
  .doctor__qualification { font-size: 11px; line-height: 13.5px; margin-top: 2px; }

  .contact { position: absolute; left: 25px; top: 197px; list-style: none; font-size: 11px; }
  .contact__item { display: flex; align-items: center; height: 14px; }
  .contact__icon { width: 9px; height: 9px; margin-right: 6px; fill: var(--brand-blue); }
  .social { display: flex; gap: 6px; margin-left: 20px; }
  .social__dot { width: 8px; height: 8px; border-radius: 50%; background: var(--brand-blue); }

  .portrait-art {
    position: absolute; left: 156px; top: 22px; width: 290px; height: 220px;
    border-radius: 60% 48% 42% 60% / 55% 50% 50% 45%;
    background: linear-gradient(100deg, var(--wave-light) 0%, var(--wave-mid) 55%, var(--wave-deep) 100%);
    opacity: 0.85;
  }
</style>
</head>
<body>
<main class="canvas">

  <section class="card card--front" aria-label="Business card front">
    <div class="brand">
      <span class="brand__dot"></span>
      <h1 class="brand__name">
        <span class="brand__title">MORAVEL</span>
        <span class="brand__tagline">AESTHETIC DOCTOR</span>
      </h1>
    </div>
    <p class="services">
      Dermal injectables - Plasma facials - Microneedling<br>
      Skin boosters - Excessive sweating
      <span class="services__offer">Home and Spa Based Treatments</span>
    </p>
  </section>

  <section class="card card--back" aria-label="Business card back">
    <div class="doctor">
      <p class="doctor__name">Dr Elise Varnholt <span class="doctor__post">MRCPCH MD</span></p>
      <p class="doctor__qualification">Australasian Diploma<br>of Aesthetic Medicine</p>
    </div>

    <div class="portrait-art" role="img" aria-label="Illustration of a profile head with flowing blue wave-like hair"></div>

    <ul class="contact">
      <li class="contact__item">
        <svg class="contact__icon" viewBox="0 0 10 10"><path d="M2 0.5 L3.6 0.5 L4.2 2.8 L3.1 3.6 Q4 5.8 6.2 6.9 L7 5.8 L9.5 6.4 L9.5 8 Q9 9.6 7.4 9.4 Q1 8.3 0.6 2.2 Q0.6 0.8 2 0.5 Z"/></svg>
        0800 555 014
      </li>
      <li class="contact__item">
        <svg class="contact__icon" viewBox="0 0 10 10"><path d="M0.5 2 H9.5 V8.5 H0.5 Z M1 2.5 L5 5.6 L9 2.5" stroke="#fbfbfb" stroke-width="0.8"/></svg>
        elise@moravel.co.nz
      </li>
      <li class="contact__item">
        <svg class="contact__icon" viewBox="0 0 10 10"><circle cx="5" cy="5" r="4.5"/><path d="M0.5 5 H9.5 M5 0.5 Q2.2 5 5 9.5 M5 0.5 Q7.8 5 5 9.5" stroke="#fbfbfb" stroke-width="0.6" fill="none"/></svg>
        www.moravel.co.nz
        <span class="social"><span class="social__dot"></span><span class="social__dot"></span></span>
      </li>
    </ul>
  </section>

</main>
</body>
</html>
```